Lanternfield Drinks business cards

We need a business card design for our new logo. The company is modern, progressive, professional, yet approachable. The key products are ready to drink bottles and cans of coffee based beverages.
These cards will be a critical part of the first impression made by our sales organization, business development team, and all external facing personnel.
Card can be a vertical or horizontal orientation.

Target Market(s)

Customers, suppliers, business partners

Industry/Entity Type

Business

Contact Information for Business Card

Business cards should feature Company Name and Logo.

Font styles to use
Serif

Colors

Designer to choose colors to be used in the design.

Requirements
Must have
• Strong readability of Name, phone #, mobile number and email address.
• Job title, website url, Street Address, and other details can be secondary level readability.
Nice to have
• High impact, simplistic quality design.
• Ok to utilize the 'H in the box' separate from the company name

```html
<!DOCTYPE html>
<html lang="en">
<head>
<meta charset="utf-8">
<title>Lanternfield Drinks business cards</title>
<link href="https://fonts.googleapis.com/css2?family=Libre+Baskerville:wght@400;700&display=swap" rel="stylesheet">
<style>
  :root {
    --stage: #a3a3a3;
    --orange: #e8562a;
    --orange-light: #f26a3a;
    --paper: #ffffff;
    --paper-shade: #f0f0f0;
    --ink: #2b2b2b;
    --gold: #c9831f;
  }
  * { margin: 0; padding: 0; box-sizing: border-box; }
  html, body { width: 1200px; height: 900px; overflow: hidden; }
  body {
    background: var(--stage);
    font-family: "Libre Baskerville", Georgia, serif;
    position: relative;
  }
  .card {
    position: absolute;
    width: 640px;
    height: 366px;
    border-radius: 18px;
    overflow: hidden;
    box-shadow: 0 10px 24px rgba(0,0,0,.25);
  }
  /* Back side */
  .card--back {
    left: 110px; top: 50px;
    background: linear-gradient(135deg, var(--orange) 0%, var(--orange-light) 100%);
    color: var(--paper);
    display: flex; flex-direction: column; align-items: center; justify-content: center;
  }
  .brand { display: flex; align-items: center; gap: 16px; }
  .brand__mark { width: 58px; height: 58px; border: 4px solid currentColor; }
  .brand__name { font-weight: 700; font-size: 28px; letter-spacing: .02em; line-height: 1.1; }
  .card--back .brand__name { color: var(--paper); }
  .card__url { margin-top: 70px; font-size: 14px; letter-spacing: .02em; }
  /* Front side */
  .card--front {
    left: 450px; top: 484px;
    background: linear-gradient(160deg, var(--paper) 0%, var(--paper-shade) 100%);
    display: flex; align-items: center;
  }
  .front__logo {
    width: 330px; display: flex; flex-direction: column; align-items: center; gap: 18px;
    color: var(--orange);
  }
  .front__logo .brand { flex-direction: column; gap: 14px; }
  .front__logo .brand__mark { width: 74px; height: 74px; border-width: 5px; }
  .front__logo .brand__name { font-size: 26px; text-align: center; }
  .divider { width: 2px; height: 200px; background: var(--orange); }
  .contact { padding-left: 30px; color: var(--ink); }
  .contact__name { color: var(--orange); font-weight: 700; font-size: 26px; }
  .contact__title { font-size: 15px; margin-top: 2px; }
  .contact__address { font-size: 12.5px; margin-top: 16px; line-height: 1.5; }
  .contact__list { list-style: none; margin-top: 14px; font-size: 13px; line-height: 1.8; }
  .contact__list li { display: flex; align-items: center; gap: 9px; }
  .contact__list svg { width: 13px; height: 13px; fill: var(--orange); flex: none; }
</style>
</head>
<body>
  <section class="card card--back" aria-label="Card back">
    <div class="brand">
      <span class="brand__mark"></span>
      <span class="brand__name">Lanternfield Drinks Co</span>
    </div>
    <p class="card__url">www.lanternfielddrinks.com</p>
  </section>

  <section class="card card--front" aria-label="Card front">
    <div class="front__logo">
      <div class="brand">
        <span class="brand__mark"></span>
        <span class="brand__name">Lanternfield<br>Drinks Co</span>
      </div>
    </div>
    <div class="divider"></div>
    <div class="contact">
      <h1 class="contact__name">Daniel Hart</h1>
      <p class="contact__title">President</p>
      <p class="contact__address">Level 2, 17 Carrow Lane<br>Brindle, VIC 3050</p>
      <ul class="contact__list">
        <li><svg viewBox="0 0 24 24"><path d="M6.6 10.8c1.4 2.8 3.8 5.1 6.6 6.6l2.2-2.2c.3-.3.7-.4 1-.2 1.1.4 2.3.6 3.6.6.6 0 1 .4 1 1V20c0 .6-.4 1-1 1C10.6 21 3 13.4 3 4c0-.6.4-1 1-1h3.5c.6 0 1 .4 1 1 0 1.3.2 2.5.6 3.6.1.3 0 .7-.2 1z"/></svg>123 555 0148</li>
        <li><svg viewBox="0 0 24 24"><path d="M2 5h20v14H2z" opacity=".0"/><path d="M2 5h20v2l-10 6L2 7zM2 9l10 6 10-6v10H2z"/></svg>info@lanternfielddrinks.com</li>
        <li><svg viewBox="0 0 24 24"><path d="M12 2a10 10 0 100 20 10 10 0 000-20zm6.9 6h-3a15 15 0 00-1.4-3.9A8 8 0 0118.9 8zM12 4c.9 1.2 1.5 2.6 1.9 4h-3.8c.4-1.4 1-2.8 1.9-4zM4.3 14a8 8 0 010-4h3.4a16 16 0 000 4zm.8 2h3a15 15 0 001.4 3.9A8 8 0 015.1 16zm3-8h-3a8 8 0 014.4-3.9C8.9 5.3 8.4 6.6 8.1 8zM12 20c-.9-1.2-1.5-2.6-1.9-4h3.8c-.4 1.4-1 2.8-1.9 4zm2.3-6H9.7a14 14 0 010-4h4.6a14 14 0 010 4zm.3 5.9c.6-1.2 1.1-2.5 1.4-3.9h3a8 8 0 01-4.4 3.9zm1.7-5.9a16 16 0 000-4h3.4a8 8 0 010 4z"/></svg>www.lanternfielddrinks.com</li>
      </ul>
    </div>
  </section>
</body>
</html>
```